Basic / Quick Business Card

Quick easy design project!

Need a one sided basic business card that matches font & style of brand and bottle label for our gourmet condiment, Brindle Harrow Sauce. Brindle Harrow Sauce is sold in specialty retail, gourmet groceries and appears on chef-driven restaurant menus, so the target market is a high end, gourmet, artisan-made food-loving customer.

Files Included:
Sauce Bottle Label
Brindle Harrow Sauce Round Logos

**About the logos - the logo may be used in a circle or alone vertically as on side of the bottle label**

Layout of Card:
May be vertical or horizontal based on designer ideas.

Logo usage (in circle vs. stand alone vertical logo) is up to designers descretion as well.

Reverse side of business card will be various high end / professional product photos / food shots using us.kelbo.com system. **Designer on this project will NOT design a reserve for the card.**

Paper that will be used for printing:
Kelbo Standard - it's a WHITE paper, but we use a cream background on Brindle Harrow Sauce branding, so please take this into account on design to stay brand consistent.

Elements & Copy for Card:
1. Logo in either script horizontal or vertical version
2. Copy: "Artisan Made - Small Batch"
3. Name - Wes Dorrance
4. Title - Creator
5. Phone - xxx.xxx.xxxx
6. xxxx@brindleharrow.com
7. URL: brindleharrowsauce.com
8. Social Media: @getbrindleharrow on Quillo / Pagora / Lumigrid

Please provide final files in Illustrator or InDesign format.

```html
<!DOCTYPE html>
<html lang="en">
<head>
<meta charset="utf-8">
<title>Brindle Harrow Sauce – Business Card</title>
<link rel="stylesheet" href="https://fonts.googleapis.com/css2?family=EB+Garamond:wght@400;500&family=Open+Sans:wght@400&display=swap">
<style>
  :root {
    --backdrop: #e9e4da;
    --card: #262425;
    --gold: #e8a92a;
    --cream: #f1ecd8;
    --ink: #2b2727;
    --white: #ffffff;
  }
  * { margin: 0; padding: 0; box-sizing: border-box; }
  html, body {
    width: 1200px; height: 828px; overflow: hidden;
    background: var(--backdrop);
  }
  .card {
    position: absolute; left: 80px; top: 114px;
    width: 1040px; height: 600px;
    background: var(--card);
    box-shadow: 0 8px 24px rgba(0,0,0,.25);
  }
  .brand-badge {
    position: absolute; left: 100px; top: 115px;
    width: 250px; height: 250px; border-radius: 50%;
    background: var(--cream);
    display: flex; align-items: center; justify-content: center;
    text-align: center;
    font-family: "EB Garamond", serif; font-weight: 500;
    font-size: 40px; line-height: 1.05; color: var(--ink);
  }
  .identity {
    position: absolute; right: 100px; top: 80px; text-align: right;
    font-family: "EB Garamond", serif;
  }
  .identity .name { color: var(--gold); font-size: 46px; line-height: 1.1; }
  .identity .title { color: var(--white); font-size: 30px; line-height: 1.2; }
  .contact {
    position: absolute; right: 100px; top: 245px;
    list-style: none; text-align: right;
    font-family: "EB Garamond", serif; font-size: 29px; color: var(--gold);
  }
  .contact li { display: flex; justify-content: flex-end; align-items: center; gap: 10px; line-height: 1.45; }
  .contact svg { width: 24px; height: 24px; fill: var(--gold); flex: none; }
  .social {
    position: absolute; right: 100px; top: 420px; text-align: right;
    font-family: "Open Sans", sans-serif; color: var(--gold);
  }
  .social .label { font-size: 31px; margin-bottom: 10px; }
  .social ul { list-style: none; display: flex; justify-content: flex-end; gap: 18px; font-size: 20px; }
  .social li { display: flex; align-items: center; gap: 7px; }
  .social .dot { width: 22px; height: 22px; border-radius: 50%; background: var(--gold); }
  .tagline {
    position: absolute; left: 100px; bottom: 70px;
    font-family: "Open Sans", sans-serif; font-size: 25px; line-height: 1.3;
    color: var(--gold);
  }
</style>
</head>
<body>
  <section class="card">
    <div class="brand-badge">Brindle<br>Harrow</div>

    <header class="identity">
      <p class="name">Wes Dorrance</p>
      <p class="title">Creator</p>
    </header>

    <ul class="contact">
      <li>
        <svg viewBox="0 0 24 24" aria-hidden="true"><path d="M12 1a11 11 0 1 0 0 22 11 11 0 0 0 0-22zm4.6 15.2c-.4.6-1.3 1-2 .9-3.4-.5-7.1-4.2-7.6-7.6-.1-.7.3-1.6.9-2l1.3-.8 2 3-1 1c.6 1.3 1.6 2.3 2.9 2.9l1-1 3 2z"/></svg>
        <span>123-555-0147</span>
      </li>
      <li>
        <svg viewBox="0 0 24 24" aria-hidden="true"><path d="M2 6h20v13H2zM3.5 7.5 12 13l8.5-5.5v-.2h-17z" fill-rule="evenodd"/></svg>
        <span>wdorrance@brindleharrow.com</span>
      </li>
      <li>
        <svg viewBox="0 0 24 24" aria-hidden="true"><path fill="none" stroke="#e8a92a" stroke-width="2" d="M12 2a10 10 0 1 0 0 20 10 10 0 0 0 0-20zM2 12h20M12 2c3 3 3 17 0 20M12 2c-3 3-3 17 0 20"/></svg>
        <span>www.brindleharrowsauce.com</span>
      </li>
    </ul>

    <div class="social">
      <p class="label">Follow Us On</p>
      <ul>
        <li><span class="dot"></span>Pagora</li>
        <li><span class="dot"></span>Quillo</li>
        <li><span class="dot"></span>Lumigrid</li>
      </ul>
    </div>

    <p class="tagline">sweet &amp; spicy<br>made in mississippi<br>Artisan Made - Small Batch</p>
  </section>
</body>
</html>
```